Yard sign

Looking for a yard sign. <br/>Something simple, name, number. <br/>Large text, readable from 50 feet away. <br/><br/>18 x 24 inches.

Target Market(s)

Potential homeowners thinking about going solar.

Colors

Designer to choose colors to be used in the design.

Requirements
Must have
• "WE'VE GONE SOLAR!"
Nice to have
• We are a solar company, we would like a design that compliments the homeowners decision that they went solar and encourages others to do the same.

```html
<!DOCTYPE html>
<html lang="en">
<head>
<meta charset="utf-8">
<title>We've Gone Solar – Yard Sign</title>
<link rel="stylesheet" href="https://fonts.googleapis.com/css2?family=Montserrat:wght@400;600;800;900&display=swap">
<style>
  :root {
    --backdrop: #221f20;
    --panel-edge: #c6c6c6;
    --panel-center: #ffffff;
    --dark-edge: #0f0f0f;
    --dark-center: #2f2f2f;
    --orange: #e36a07;
    --orange-deep: #e2540a;
    --orange-brand: #f07b14;
    --amber: #fbb512;
    --yellow: #fcc62b;
    --shadow: #3a3a3a;
  }
  html, body {
    margin: 0;
    width: 1200px;
    height: 1200px;
    overflow: hidden;
    background: var(--backdrop);
  }
  .yard-sign {
    position: absolute;
    left: 50px;
    top: 188px;
    width: 1100px;
    height: 825px;
    display: block;
  }
  .headline {
    font-family: "Montserrat", sans-serif;
    filter: drop-shadow(4px 4px 0 var(--shadow));
  }
  .headline-top { font-weight: 800; font-size: 156px; fill: var(--orange); }
  .headline-main { font-weight: 900; font-size: 278px; }
  .brand-name { font-family: "Montserrat", sans-serif; font-weight: 800; font-size: 100px; fill: var(--orange-brand); }
  .brand-tagline { font-family: "Montserrat", sans-serif; font-weight: 400; font-size: 21px; fill: var(--yellow); }
  .contact-phone { font-family: "Montserrat", sans-serif; font-weight: 800; font-size: 66px; fill: var(--yellow); }
  .contact-web { font-family: "Montserrat", sans-serif; font-weight: 600; font-size: 38px; fill: var(--orange-deep); }
</style>
</head>
<body>
<svg class="yard-sign" viewBox="0 0 1100 825" xmlns="http://www.w3.org/2000/svg" role="img" aria-label="We've gone solar yard sign">
  <defs>
    <linearGradient id="panel-fill" x1="0" y1="0" x2="1" y2="0">
      <stop offset="0" stop-color="var(--panel-edge)"/>
      <stop offset="0.5" stop-color="var(--panel-center)"/>
      <stop offset="1" stop-color="var(--panel-edge)"/>
    </linearGradient>
    <linearGradient id="dark-fill" x1="0" y1="0" x2="1" y2="0">
      <stop offset="0" stop-color="var(--dark-edge)"/>
      <stop offset="0.5" stop-color="var(--dark-center)"/>
      <stop offset="1" stop-color="var(--dark-edge)"/>
    </linearGradient>
    <linearGradient id="solar-fill" gradientUnits="userSpaceOnUse" x1="0" y1="222" x2="0" y2="417">
      <stop offset="0" stop-color="var(--amber)"/>
      <stop offset="0.7" stop-color="var(--orange-deep)"/>
      <stop offset="1" stop-color="var(--orange-deep)"/>
    </linearGradient>
  </defs>

  <rect class="panel" x="0" y="0" width="1100" height="825" fill="url(#panel-fill)"/>

  <path class="band-yellow" d="M0 549 Q550 407 1100 558 L1100 825 L0 825 Z" fill="var(--yellow)"/>
  <path class="band-orange" d="M0 590 Q550 385 1100 600 L1100 825 L0 825 Z" fill="var(--orange-deep)"/>
  <path class="footer-dark" d="M0 604 Q550 392 1100 615 L1100 825 L0 825 Z" fill="url(#dark-fill)"/>

  <text class="headline headline-top" x="68" y="199" textLength="969" lengthAdjust="spacingAndGlyphs">WE'VE GONE</text>
  <text class="headline headline-main" x="65" y="417" textLength="969" lengthAdjust="spacingAndGlyphs" fill="url(#solar-fill)">SOLAR!</text>

  <circle class="brand-dot" cx="130" cy="680" r="38" fill="var(--yellow)"/>
  <text class="brand-name" x="185" y="712" textLength="268" lengthAdjust="spacingAndGlyphs">BRYX</text>
  <text class="brand-tagline" x="185" y="740" textLength="268" lengthAdjust="spacing">BRIGHT YARD SOLAR</text>

  <rect class="divider" x="504" y="625" width="3" height="118" fill="var(--orange-deep)"/>

  <text class="contact-phone" x="537" y="682" textLength="410" lengthAdjust="spacingAndGlyphs">123 456 7890</text>
  <text class="contact-web" x="537" y="729" textLength="410" lengthAdjust="spacing">www.brightyardsolar.net</text>
</svg>
</body>
</html>
```